Website Design - TallyPorchHelpers.net

PLEASE CHECK WORD DOCUMENT ATTACHED FOR WEBSITE FLOW.

Target Market(s)

REAL ESTATE AGENTS ARE THE TARGET MARKET

Industry/Entity Type

Real Estate

Coding

Coded - Design and coding required

Number of Pages Required

4 page

Colors

Designer to choose colors to be used in the design.

Requirements
Must have
• WE LIKE RED LOGO ATTACHED
Nice to have
• PLEASE CHECK WORD DOCUMENT ATTACHED FOR WEBSITE FLOW.
Should not have

```html
<!DOCTYPE html>
<html lang="en">
<head>
<meta charset="utf-8">
<title>TallyPorchHelpers.net</title>
<link href="https://fonts.googleapis.com/css2?family=Rubik:wght@400;500;600;700&display=swap" rel="stylesheet">
<style>
:root{
  --red:#e8161c;
  --red-deep:#c80d12;
  --ink:#1b1b1b;
  --paper:#f2f2f2;
  --white:#ffffff;
  --footer:#262626;
  --footer-text:#a9a9a9;
  --muted:#555555;
}
*{box-sizing:border-box;margin:0;padding:0}
html,body{width:932px;height:1200px;overflow:hidden}
body{font-family:'Rubik',sans-serif;background:var(--paper);color:var(--ink);position:relative}

.hero{position:absolute;left:0;top:0;width:932px;height:466px;
  background:linear-gradient(100deg,#c9643d 0%,#8a3a2c 28%,#6e2b26 55%,#5a2424 80%,#3e1b1b 100%)}
.hero::after{content:"";position:absolute;inset:0;background:linear-gradient(180deg,rgba(40,10,10,.25),rgba(120,20,20,.15) 60%,rgba(60,15,15,.35))}
.nav{position:absolute;top:0;left:0;width:932px;height:64px;z-index:2}
.brand{position:absolute;left:182px;top:18px;display:flex;align-items:center;gap:5px;color:var(--white);font-weight:700;font-size:12px;line-height:12px}
.brand .dot{width:12px;height:12px;background:var(--red)}
.menu{position:absolute;left:306px;top:26px;display:flex;gap:23px;list-style:none}
.menu li{color:var(--white);font-size:8px;font-weight:500;letter-spacing:.2px}
.call{position:absolute;left:640px;top:20px;display:flex;gap:6px;color:var(--white)}
.call small{display:block;font-size:7.5px}
.call strong{display:block;font-size:11px;font-weight:600}
.hero-copy{position:absolute;top:226px;left:0;width:932px;text-align:center;color:var(--white);z-index:2}
.hero-copy h1{font-size:26px;font-weight:700;letter-spacing:-.3px}
.hero-copy p{font-size:13.5px;line-height:18px;margin-top:8px}

.audience{position:absolute;left:0;top:466px;width:932px;height:160px;background:linear-gradient(90deg,var(--red-deep),var(--red) 50%,var(--red-deep))}
.audience h2{position:absolute;top:36px;width:100%;text-align:center;color:var(--white);font-size:15px;font-weight:700}
.option{position:absolute;top:79px;width:180px;height:111px;background:var(--white);border-radius:3px;overflow:hidden;text-align:center;box-shadow:0 2px 6px rgba(0,0,0,.15)}
.option svg.icon{margin-top:16px}
.option p{font-size:9.5px;line-height:12px;margin-top:4px}
.option p b{font-weight:600}
.option .slant{position:absolute;left:0;bottom:0}

.packages-title{position:absolute;top:692px;width:932px;text-align:center;font-size:16px;font-weight:600}
.plan{position:absolute;top:735px;width:108px;height:292px;background:var(--white);border-radius:4px;overflow:hidden;box-shadow:0 1px 4px rgba(0,0,0,.06)}
.plan-head{position:relative;height:54px;color:var(--white);text-align:center}
.plan-head svg{position:absolute;left:0;top:0}
.plan-head span{position:relative;display:block;padding-top:13px;font-size:11px;font-weight:600}
.features{list-style:none;padding:10px 14px 0 10px}
.features li{position:relative;padding-left:10px;font-size:8px;line-height:11.6px;color:#333;margin-bottom:11.6px}
.features li svg{position:absolute;left:0;top:2px}
.plan .btn{display:block;margin:0 auto;width:88px;height:25px;line-height:25px;text-align:center;background:var(--ink);color:var(--white);font-size:8px;font-weight:500;border-radius:2px}
.plan.featured .btn{background:var(--red)}
.plan .note{font-size:6.3px;line-height:9.6px;text-align:center;color:#777;margin-top:7px}

.footer{position:absolute;left:0;top:1066px;width:932px;height:134px;background:var(--footer);color:var(--footer-text)}
.info{position:absolute;top:27px;display:flex;gap:7px;font-size:8px;line-height:12.5px}
.socials{position:absolute;left:657px;top:26px;display:flex;gap:4px}
.socials span{width:20px;height:20px;border:1.3px solid var(--footer-text);border-radius:50%}
.rule{position:absolute;top:92px;left:0;width:932px;height:1px;background:#393939}
.foot-brand{position:absolute;top:84px;left:446px;width:40px;text-align:center;background:var(--footer);color:var(--red);font-size:7px;font-weight:700;line-height:8px}
.copy{position:absolute;top:110px;left:182px;font-size:8px}
.legal{position:absolute;top:110px;right:182px;font-size:8px;display:flex;gap:6px}
</style>
</head>
<body>

<header class="hero" role="img" aria-label="Photo of a smiling couple meeting a real estate agent in front of a house with an open house sign, red tint">
  <nav class="nav">
    <div class="brand"><span class="dot"></span>TallyPorch<br>Helpers</div>
    <ul class="menu">
      <li>HOW IT WORKS</li><li>SERVICE AREA</li><li>PRICING</li><li>ABOUT US</li><li>FAQ</li>
    </ul>
    <div class="call">
      <svg width="18" height="18" viewBox="0 0 24 24" fill="none" stroke="#fff" stroke-width="1.4"><path d="M5 3h4l2 5-2.5 1.5a11 11 0 0 0 6 6L16 13l5 2v4a2 2 0 0 1-2 2A16 16 0 0 1 3 5a2 2 0 0 1 2-2z"/></svg>
      <div><small>Call Us Today</small><strong>1800 555 0142</strong></div>
    </div>
  </nav>
  <div class="hero-copy">
    <h1>Helping agents save time and money.</h1>
    <p>We place signs and boost foot traffic to your open houses<br>using proven marketing techniques.</p>
  </div>
</header>

<section class="audience">
  <h2>Choose The Option Below That Best Describes You</h2>
  <div class="option" style="left:182px">
    <svg class="icon" width="28" height="32" viewBox="0 0 28 32"><circle cx="14" cy="9" r="8" fill="var(--red)"/><path d="M0 32v-5a9 9 0 0 1 9-9h10a9 9 0 0 1 9 9v5z" fill="var(--red)"/></svg>
    <p>I'M A<br><b>FULL ON BROKERAGE</b></p>
    <svg class="slant" width="180" height="14" viewBox="0 0 180 14"><polygon points="0,2 180,12 180,14 0,14" fill="var(--red)"/></svg>
  </div>
  <div class="option" style="left:376px">
    <svg class="icon" width="32" height="32" viewBox="0 0 32 32" fill="var(--red)"><circle cx="8" cy="9" r="4"/><circle cx="24" cy="9" r="4"/><circle cx="16" cy="13" r="5"/><path d="M0 24a6 6 0 0 1 6-6h4a6 6 0 0 1 6 6zM16 24a6 6 0 0 1 6-6h4a6 6 0 0 1 6 6z"/><path d="M7 30a8 8 0 0 1 8-8h2a8 8 0 0 1 8 8z"/></svg>
    <p>I'M AN<br><b>IND. BROKER WITH A TEAM</b></p>
    <svg class="slant" width="180" height="14" viewBox="0 0 180 14"><polygon points="0,2 180,12 180,14 0,14" fill="var(--red)"/></svg>
  </div>
  <div class="option" style="left:570px">
    <svg class="icon" width="30" height="32" viewBox="0 0 30 32" fill="var(--red)"><rect x="0" y="0" width="3" height="32"/><rect x="27" y="0" width="3" height="32"/><rect x="3" y="3" width="24" height="11"/></svg>
    <p>I NEED<br><b>SIGN PLACEMENT ASAP</b></p>
    <svg class="slant" width="180" height="14" viewBox="0 0 180 14"><polygon points="0,2 180,12 180,14 0,14" fill="var(--red)"/></svg>
  </div>
</section>

<h2 class="packages-title">Choose Your Package</h2>

<article class="plan" style="left:182px">
  <div class="plan-head"><svg width="108" height="54" viewBox="0 0 108 54"><path d="M0 0H108V52C90 52 72 38 54 38S18 52 0 52Z" fill="var(--ink)"/></svg><span>5 SIGNS</span></div>
  <ul class="features">
    <li><svg width="8" height="8" viewBox="0 0 8 8"><path d="M1 4l2 2 4-5" stroke="var(--red)" stroke-width="1.4" fill="none"/></svg>Place signs strategically in best areas according to where the open house is located</li>
    <li><svg width="8" height="8" viewBox="0 0 8 8"><path d="M1 4l2 2 4-5" stroke="var(--red)" stroke-width="1.4" fill="none"/></svg>Pick Up the signs after the open house</li>
    <li><svg width="8" height="8" viewBox="0 0 8 8"><path d="M1 4l2 2 4-5" stroke="var(--red)" stroke-width="1.4" fill="none"/></svg>Store custom signs for you if needed</li>
  </ul>
  <span class="btn">SIGN UP</span>
  <p class="note">Sign Up For A Subscription<br>And Get These Marketing<br>Services For Free</p>
</article>

<article class="plan" style="left:297px">
  <div class="plan-head"><svg width="108" height="54" viewBox="0 0 108 54"><path d="M0 0H108V52C90 52 72 38 54 38S18 52 0 52Z" fill="var(--ink)"/></svg><span>10 SIGNS</span></div>
  <ul class="features">
    <li><svg width="8" height="8" viewBox="0 0 8 8"><path d="M1 4l2 2 4-5" stroke="var(--red)" stroke-width="1.4" fill="none"/></svg>Place signs strategically in best areas according to where the open house is located</li>
    <li><svg width="8" height="8" viewBox="0 0 8 8"><path d="M1 4l2 2 4-5" stroke="var(--red)" stroke-width="1.4" fill="none"/></svg>Pick Up the signs after the open house</li>
    <li><svg width="8" height="8" viewBox="0 0 8 8"><path d="M1 4l2 2 4-5" stroke="var(--red)" stroke-width="1.4" fill="none"/></svg>Store custom signs for you if needed</li>
  </ul>
  <span class="btn">SIGN UP</span>
  <p class="note">Sign Up For A Subscription<br>And Get These Marketing<br>Services For Free</p>
</article>

<article class="plan featured" style="left:412px">
  <div class="plan-head"><svg width="108" height="54" viewBox="0 0 108 54"><path d="M0 0H108V52C90 52 72 38 54 38S18 52 0 52Z" fill="var(--red)"/></svg><span>15 SIGNS</span></div>
  <ul class="features">
    <li><svg width="8" height="8" viewBox="0 0 8 8"><path d="M1 4l2 2 4-5" stroke="var(--red)" stroke-width="1.4" fill="none"/></svg>Place signs strategically in best areas according to where the open house is located</li>
    <li><svg width="8" height="8" viewBox="0 0 8 8"><path d="M1 4l2 2 4-5" stroke="var(--red)" stroke-width="1.4" fill="none"/></svg>Pick Up the signs after the open house</li>
    <li><svg width="8" height="8" viewBox="0 0 8 8"><path d="M1 4l2 2 4-5" stroke="var(--red)" stroke-width="1.4" fill="none"/></svg>Store custom signs for you if needed</li>
  </ul>
  <span class="btn">SIGN UP</span>
  <p class="note">Sign Up For A Subscription<br>And Get These Marketing<br>Services For Free</p>
</article>

<article class="plan" style="left:527px">
  <div class="plan-head"><svg width="108" height="54" viewBox="0 0 108 54"><path d="M0 0H108V52C90 52 72 38 54 38S18 52 0 52Z" fill="var(--ink)"/></svg><span>20 SIGNS</span></div>
  <ul class="features">
    <li><svg width="8" height="8" viewBox="0 0 8 8"><path d="M1 4l2 2 4-5" stroke="var(--red)" stroke-width="1.4" fill="none"/></svg>Place signs strategically in best areas according to where the open house is located</li>
    <li><svg width="8" height="8" viewBox="0 0 8 8"><path d="M1 4l2 2 4-5" stroke="var(--red)" stroke-width="1.4" fill="none"/></svg>Pick Up the signs after the open house</li>
    <li><svg width="8" height="8" viewBox="0 0 8 8"><path d="M1 4l2 2 4-5" stroke="var(--red)" stroke-width="1.4" fill="none"/></svg>Store custom signs for you if needed</li>
  </ul>
  <span class="btn">SIGN UP</span>
  <p class="note">Sign Up For A Subscription<br>And Get These Marketing<br>Services For Free</p>
</article>

<article class="plan" style="left:642px">
  <div class="plan-head"><svg width="108" height="54" viewBox="0 0 108 54"><path d="M0 0H108V52C90 52 72 38 54 38S18 52 0 52Z" fill="var(--ink)"/></svg><span>25 SIGNS</span></div>
  <ul class="features">
    <li><svg width="8" height="8" viewBox="0 0 8 8"><path d="M1 4l2 2 4-5" stroke="var(--red)" stroke-width="1.4" fill="none"/></svg>Place signs strategically in best areas according to where the open house is located</li>
    <li><svg width="8" height="8" viewBox="0 0 8 8"><path d="M1 4l2 2 4-5" stroke="var(--red)" stroke-width="1.4" fill="none"/></svg>Pick Up the signs after the open house</li>
    <li><svg width="8" height="8" viewBox="0 0 8 8"><path d="M1 4l2 2 4-5" stroke="var(--red)" stroke-width="1.4" fill="none"/></svg>Store custom signs for you if needed</li>
  </ul>
  <span class="btn">SIGN UP</span>
  <p class="note">Sign Up For A Subscription<br>And Get These Marketing<br>Services For Free</p>
</article>

<footer class="footer">
  <div class="info" style="left:182px">
    <svg width="14" height="20" viewBox="0 0 14 20" fill="none" stroke="var(--red)" stroke-width="1.3"><path d="M7 19S1 11 1 7a6 6 0 0 1 12 0c0 4-6 12-6 12z"/><circle cx="7" cy="7" r="2"/></svg>
    <div>417, Cedar Lane Road<br>Bayview suite - 27134</div>
  </div>
  <div class="info" style="left:327px">
    <svg width="20" height="20" viewBox="0 0 24 24" fill="none" stroke="var(--red)" stroke-width="1.3"><path d="M5 3h4l2 5-2.5 1.5a11 11 0 0 0 6 6L16 13l5 2v4a2 2 0 0 1-2 2A16 16 0 0 1 3 5a2 2 0 0 1 2-2z"/></svg>
    <div>Call Us<br>1800 555 0199 (toll-free)</div>
  </div>
  <div class="info" style="left:473px">
    <svg width="20" height="20" viewBox="0 0 20 20" fill="none" stroke="var(--red)" stroke-width="1.3"><rect x="1" y="5" width="18" height="13"/><path d="M1 5l9 7 9-7M1 18l7-6M19 18l-7-6"/></svg>
    <div>Email Us<br>info@tallyporchhelpers.net</div>
  </div>
  <div class="socials"><span></span><span></span><span></span><span></span></div>
  <div class="rule"></div>
  <div class="foot-brand">TallyPorch<br>Helpers</div>
  <div class="copy">© 2018 TallyPorchHelpers</div>
  <div class="legal"><span>Privacy Policy</span><span>Term of Service</span></div>
</footer>

</body>
</html>
```